Web Design Project

We need a web design for a legal firm based in Sydney, Australia. Our main clients are small businesses, accountants and entrepreneurs. We help our clients deal with commercial disputes and litigation.
In terms of the site design, we would like the site to appear professional, clean and easy to navigate however we would like it to be slightly more creative than the average legal website.
Legal Sites we like:
http://www.qrp.com.au/
http://www.tillmarkforge.com/
http://www.zavu.com/
Non-Legal Sites we like:
http://www.kelvra.com/index-b.html
http://www.pembridon.com/
http://www.quorvel.com/
Sites we don't like:
http://www.westmarklevyfixers.com/
We have listed below some possible colour palettes for the site:
http://www.tintgatherers.com/palette/74162/Legal_Man
http://www.tintgatherers.com/palette/651375/Legal_Transplant
http://www.tintgatherers.com/palette/199581/Legal_Notice
Site design elements we like:
Large Footer (with newsletter sign up form)
Full screen (postwren.com, pembridon.com)
Customised Social Media icons that fit in with the style of our website
Slider
We need the following templates created:
Home Page
General Content Page
Blog

```html
<!DOCTYPE html>
<html lang="en">
<head>
<meta charset="utf-8">
<title>Veyra – We solve everything</title>
<link href="https://fonts.googleapis.com/css2?family=Open+Sans:ital,wght@0,300;0,400;0,600;0,700;1,400&display=swap" rel="stylesheet">
<style>
:root{
  --teal:#5fb9c9;
  --teal-dark:#2f8a90;
  --teal-light:#8fd0d5;
  --ink:#3a4a4e;
  --heading:#35616a;
  --pale:#f4f6e4;
  --panel:#e4e7d0;
  --rule:#b9bfbf;
  --white:#ffffff;
}
*{box-sizing:border-box;margin:0;padding:0}
html,body{width:1002px;height:1200px;overflow:hidden}
body{position:relative;background:var(--white);font-family:"Open Sans",sans-serif;color:var(--ink)}
.abs{position:absolute}

/* hero */
.hero{left:0;top:0;width:1002px;height:377px;
  background:linear-gradient(180deg,#2c9ddd 0%,#5fb6e6 35%,#b9def2 65%,#f3f8fb 100%);}
.hero-sky-glow{left:0;top:0;width:1002px;height:377px;
  background:radial-gradient(ellipse 420px 160px at 300px 260px,rgba(255,255,255,.55),rgba(255,255,255,0) 70%),
             radial-gradient(ellipse 300px 110px at 760px 330px,rgba(255,255,255,.6),rgba(255,255,255,0) 70%);}
.divider-hero{left:0;top:377px;width:1002px;height:1px;background:var(--rule)}

.navbar{left:84px;top:24px;width:834px;height:62px;
  background:linear-gradient(180deg,#92d3d6,#6cc1cc);box-shadow:0 2px 3px rgba(0,0,0,.12)}
.brand{left:84px;top:24px;width:141px;height:62px;background:#f6f6f6;display:flex;align-items:center;justify-content:center;gap:8px}
.brand-mark{width:18px;height:18px;background:#1d4f8c}
.brand-name{font-weight:700;font-size:19px;color:#1d4f8c;letter-spacing:.5px}
.menu{left:490px;top:43px;display:flex;font-size:10px;color:#2f4a50}
.menu li{list-style:none;width:60px;text-align:center;line-height:24px}
.menu li.active{background:var(--pale)}
.submenu{left:735px;top:67px;width:104px;height:86px;background:#e5e7d1;padding:6px 0 0 13px;font-size:9.5px;line-height:18.4px;color:#3d4e52;list-style:none}
.submenu .current{color:#1c2a2d}

.slide-eyebrow{left:558px;top:124px;font-size:29px;font-weight:300;color:var(--teal-dark);opacity:.85}
.slide-title{left:554px;top:150px;font-size:63px;font-weight:300;color:var(--teal-dark);letter-spacing:-1px;line-height:1}
.slide-text{left:558px;top:232px;width:305px;font-size:11.7px;line-height:15px;color:#223238}
.more{left:558px;top:306px;font-size:11.5px;line-height:15px;color:var(--teal)}
.more-btn{left:609px;top:300px}
.slide-arrow{top:180px}
.dots{left:123px;top:332px;display:flex;gap:8px}
.dots span{width:9px;height:9px;border-radius:50%;background:#c8e4e2}
.dots span.on{background:#26636a}

/* sidebar */
.offer-head{left:100px;top:397px;width:192px;height:42px;background:#8ccfd2;color:#fff;font-size:13.5px;padding:12px 0 0 24px;font-weight:300}
.offer-list{left:100px;top:443px;width:192px;list-style:none}
.offer-list li{height:34px;background:var(--pale);margin-bottom:3.6px;font-size:12px;color:var(--teal);padding:8px 0 0 24px}
.offer-list li.active{background:#5ab6c7;color:#fff;border:1px solid #3d8a98;padding-left:23px;font-weight:600}

.promo{left:100px;width:192px;background:var(--panel)}
.promo-title{font-size:12px;color:var(--heading)}
.promo-text{font-size:9.5px;line-height:11.6px;color:#2b3a3d}
.promo-art{position:absolute;background:linear-gradient(160deg,#f7f7f3,#d8dbd2);border-radius:2px}
.promo-btn{position:absolute;left:9px;width:175px;height:34px;background:var(--teal);color:#fff;font-size:12px;display:flex;align-items:center;justify-content:center;gap:10px}

/* content */
.page-title{left:366px;top:402px;font-size:20px;font-weight:300;color:var(--heading)}
.title-rule{left:342px;top:438px;width:560px;height:1px;background:#9aa3a3}
.lead{left:367px;top:457px;width:512px;font-style:italic;font-weight:400;font-size:13.4px;line-height:18.4px;color:#34464a}
.body-copy{left:367px;top:546px;width:516px;font-size:9.4px;line-height:15px;color:#4a5a5e}
.body-copy p{margin-bottom:15px}
.body-copy a{color:#4a5a5e}

/* footer */
.footer{left:0;top:1004px;width:1002px;height:196px;background:linear-gradient(180deg,#e6e9d6,#dfe2c8)}
.footer-rule{top:1024px;width:1px;height:146px;background:#c8ccb8}
.footer-head{top:1028px;font-size:15px;font-weight:300;color:#5a6a6c}
.assoc-text{left:108px;top:1064px;width:96px;font-size:9.8px;line-height:15px;color:#2e3c3e}
.badge{position:absolute;width:32px;height:26px}
.contact-label{font-size:12px;font-weight:600;color:#1f2b2d}
.contact-text{font-size:9.5px;line-height:15px;color:#2e3c3e}
.news-title{left:693px;top:1063px;font-size:12px;font-weight:600;color:#1f2b2d}
.field{left:693px;width:209px;height:21px;background:#f3f5e6;font-size:9.5px;color:#8a9393;padding:4px 0 0 16px}
.signup{left:693px;top:1140px;width:65px;height:21px;background:var(--teal);color:#fff;font-size:10px;text-align:center;line-height:21px}
.find{left:793px;top:1143px;font-size:9.5px;color:#1f2b2d}
</style>
</head>
<body>

<!-- hero slider -->
<div class="abs hero" role="img" aria-label="Blue sky with clouds and paper planes folded from banknotes"></div>
<div class="abs hero-sky-glow"></div>
<div class="abs divider-hero"></div>

<div class="abs navbar"></div>
<div class="abs brand"><span class="brand-mark"></span><span class="brand-name">Veyra</span></div>
<ul class="abs menu">
  <li>Menu</li><li>Menu</li><li>Menu</li><li>Menu</li><li class="active">Menu</li><li>Menu</li><li>Menu</li>
</ul>
<ul class="abs submenu">
  <li>Submenu</li><li class="current">&gt; Submenu</li><li>Submenu</li><li>Submenu</li>
</ul>

<div class="abs slide-eyebrow">We solve</div>
<div class="abs slide-title">Everything..</div>
<p class="abs slide-text">Lorem ipsum dolor sit amet, consectetur adipiscing elit. Donec mi quam, placerat id convallis pellentesque, dictum sed arcu. Sed hendrerit sagittis eleifend.</p>
<div class="abs more">more<br>details</div>
<svg class="abs more-btn" width="42" height="42" viewBox="0 0 42 42"><circle cx="21" cy="21" r="21" fill="#8fd0c5"/><path d="M11 21h19M23 14l7 7-7 7" stroke="#fff" stroke-width="2.4" fill="none" stroke-linecap="round" stroke-linejoin="round"/></svg>

<svg class="abs slide-arrow" style="left:17px" width="42" height="42" viewBox="0 0 42 42"><circle cx="21" cy="21" r="21" fill="#fff" fill-opacity=".55"/><path d="M24 12l-9 9 9 9" stroke="#7fbcd8" stroke-width="4" fill="none" stroke-linecap="round" stroke-linejoin="round"/></svg>
<svg class="abs slide-arrow" style="left:943px" width="42" height="42" viewBox="0 0 42 42"><circle cx="21" cy="21" r="21" fill="#fff" fill-opacity=".55"/><path d="M18 12l9 9-9 9" stroke="#7fbcd8" stroke-width="4" fill="none" stroke-linecap="round" stroke-linejoin="round"/></svg>
<div class="abs dots"><span></span><span></span><span class="on"></span><span></span></div>

<!-- sidebar -->
<div class="abs offer-head">What we offer?</div>
<ul class="abs offer-list">
  <li>Cras dignissim eleifend</li>
  <li>Enim in posuere</li>
  <li class="active">Risus rutrum in</li>
  <li>Praesent dapibus leo sed</li>
  <li>Neque</li>
</ul>

<div class="abs promo" style="top:645px;height:158px">
  <div class="promo-title" style="position:absolute;left:23px;top:14px">Get to know<br><span style="font-size:17px;line-height:14px">us...</span></div>
  <div class="promo-art" role="img" aria-label="Registration form with a fountain pen" style="left:108px;top:22px;width:70px;height:80px"></div>
  <p class="promo-text" style="position:absolute;left:23px;top:60px;width:80px">Register for local events, webinars &amp; product demos.</p>
  <div class="promo-btn" style="top:116px">Register for an event
    <svg width="18" height="12" viewBox="0 0 18 12"><path d="M1 6h15M11 1l5 5-5 5" stroke="#fff" stroke-width="1.6" fill="none" stroke-linecap="round"/></svg></div>
</div>

<div class="abs promo" style="top:820px;height:159px">
  <div class="promo-title" style="position:absolute;left:23px;top:14px;font-size:14px;font-weight:600">Free Whitepaper...</div>
  <p class="promo-text" style="position:absolute;left:23px;top:46px;width:75px">10 metrics you can't get from your billing system</p>
  <div class="promo-art" role="img" aria-label="Lined notepad with a blue bookmark ribbon" style="left:98px;top:50px;width:72px;height:62px"></div>
  <div class="promo-btn" style="top:117px">View today
    <svg width="18" height="12" viewBox="0 0 18 12"><path d="M1 6h15M11 1l5 5-5 5" stroke="#fff" stroke-width="1.6" fill="none" stroke-linecap="round"/></svg></div>
</div>

<!-- main content -->
<h1 class="abs page-title">Mauris quis dui sit amet leo venenatis interdum.</h1>
<div class="abs title-rule"></div>
<p class="abs lead">Lorem ipsum dolor sit amet, consectetur adipiscing elit. Etiam vel odio vel massa blandit mollis id et sem. Donec faucibus tortor vitae nunc rutrum quis suscipit neque cursus. Aenean ac orci lectus, at tincidunt ante. Donec dui felis, cursus nec ornare eget, tempor in erat.</p>
<div class="abs body-copy">
  <p>Aenean vulputate, leo eu porta ultrices, purus tortor eleifend sapien, non dignissim augue nulla at justo. <a href="#">Duis fermentum leo ut</a> turpis molestie suscipit. Maecenas non mi et neque ultrices pharetra quis et est. Nam pulvinar vehicula risus, nec pellentesque massa hendrerit vitae. Curabitur pellentesque ultrices interdum. Nam interdum eros sed ligula gravida vel posuere libero volutpat. Donec et diam molestie elit pretium adipiscing et vitae nisl. Morbi in risus et massa lobortis viverra.</p>
  <p>Mauris quis dui sit amet leo venenatis interdum. Aenean ut dui vitae nisl suscipit volutpat. Nullam hendrerit magna vel tellus rutrum quis varius nulla placerat. In lobortis, urna quis luctus fringilla, risus tortor consequat nisi, sed ultricies purus mi at augue. Pellentesque enim ipsum, sodales in interdum at, convallis eget mi. Ut suscipit fringilla arcu, ut lacinia ante gravida eget. Donec mollis euismod odio, a tincidunt ante tincidunt at. Vestibulum a turpis quis arcu blandit vehicula. Suspendisse at adipiscing ipsum. Cras sodales tincidunt adipiscing. Vivamus volutpat odio vel lectus suscipit ac varius eros ullamcorper. Quisque gravida justo vel sapien consequat tempus. Cras tincidunt, tortor et pretium hendrerit, purus nunc pretium tortor, eget vulputate lacus neque at libero. Curabitur scelerisque vehicula sem, facilisis consequat lacus commodo ut. Suspendisse placerat commodo leo, et consequat augue tempus in. Curabitur a felis risus.</p>
  <p>Vestibulum dignissim lectus in lectus pretium fringilla. Duis pellentesque eros vel ante posuere tincidunt vel ut libero. Morbi vitae urna est, eget auctor nibh. Fusce suscipit venenatis scelerisque. Aenean nisl leo, rutrum non dictum ut, tincidunt nec velit. Praesent ac vehicula quam. Nunc lobortis porta feugiat. Aenean sit amet posuere turpis. Nullam tincidunt metus a augue mollis ornare. Nullam at augue felis, ut tempus nulla. Aliquam erat volutpat. Class aptent taciti sociosqu ad litora torquent per conubia nostra, per inceptos himenaeos. Quisque consectetur molestie metus non interdum. Nunc condimentum auctor tortor, id hendrerit libero pulvinar in.</p>
  <p>Class aptent taciti sociosqu ad litora torquent per conubia nostra, per inceptos himenaeos. Donec purus quam, commodo quis luctus nec, sollicitudin nec nisl. Vestibulum eu purus at felis lobortis euismod eget ut dolor. Nullam ut tincidunt est. Cras dapibus imperdiet adipiscing. Proin et libero erat. Aenean ullamcorper varius ligula, eu pharetra nulla consequat sit amet. Morbi adipiscing viverra lectus, rhoncus dignissim orci blandit vel. Nulla vitae massa id diam pretium posuere in id ante.</p>
</div>

<!-- footer -->
<div class="abs footer"></div>
<div class="abs footer-rule" style="left:342px"></div>
<div class="abs footer-rule" style="left:676px"></div>

<h2 class="abs footer-head" style="left:108px">Associations</h2>
<p class="abs assoc-text">Lorem ipsum dolor sit amet, consectetur adipiscing elit. Morbi risus lorem, sollicitudin sed gravida non</p>
<div class="badge" style="left:224px;top:1068px;background:#3a78b8;border-radius:50%;width:28px;height:28px"></div>
<div class="badge" style="left:280px;top:1068px;background:#d93a32"></div>
<div class="badge" style="left:224px;top:1116px;background:#7aa04a"></div>
<div class="badge" style="left:280px;top:1116px;background:#243a6a;width:30px;height:30px"></div>

<h2 class="abs footer-head" style="left:358px">Contact us</h2>
<div class="abs contact-label" style="left:359px;top:1063px">Company name</div>
<p class="abs contact-text" style="left:359px;top:1082px">Address, street 1243/ 35B<br>New York city<br>1234823</p>
<svg class="abs" style="left:501px;top:1064px" width="20" height="22" viewBox="0 0 20 22"><path d="M4 1c1.5-.6 2.6 0 3.2 1.4l1.3 3c.4 1-.1 1.8-1 2.4l-1 .7c.8 2.8 2.8 5.3 5.4 6.8l.9-.9c.8-.7 1.7-.9 2.6-.3l2.6 2c1.2.9 1.2 2.1.3 3.2-1.6 1.9-3.6 2.4-6 1.1C7 17.9 3.1 13 1.4 7.4.8 4.6 1.6 2.2 4 1z" fill="#b8bca8"/></svg>
<div class="abs contact-label" style="left:533px;top:1063px">Phone:</div>
<div class="abs contact-text" style="left:533px;top:1082px">0417 552 083 164</div>
<svg class="abs" style="left:500px;top:1113px" width="22" height="15" viewBox="0 0 22 15"><rect x="0" y="0" width="22" height="15" fill="#b8bca8"/><path d="M1 1l10 8 10-8" stroke="#e4e7d2" stroke-width="1.4" fill="none"/></svg>
<div class="abs contact-label" style="left:533px;top:1112px">E-mail:</div>
<div class="abs contact-text" style="left:533px;top:1131px">hello@veyralegal.com</div>

<h2 class="abs footer-head" style="left:693px">Connect</h2>
<div class="abs news-title">Sign Up to Our Newsletter</div>
<div class="abs field" style="top:1084px">Your name here..</div>
<div class="abs field" style="top:1109px">Your e-mail here..</div>
<div class="abs signup">Sign Up</div>
<div class="abs find">Find us on Linkora</div>

</body>
</html>
```